Thornvale Group needs a business card design

We need a new business card design using the logo recently selected in a logo competition on Pixel Bazaar. Our business is a consultancy specializing in aviation and energy and the winning business card design will promote an image of precision and professionalism with creativity.

Please use the logo with the name on the front of the card and use a complementary font. Make the back white with either the light grey or dark grey logo.

Target Market(s)

Senior finance and legal leaders at aviation and energy companies

Industry/Entity Type

Management Consulting

Contact Information for Business Card

Peter Castrell
President
Thornvale Group

www.thornvalegroup.example

(555) 204-6391
pc@thornvalegroup.example

Requirements
Must have
• Professional font that goes well with the logo font

```html
<!DOCTYPE html>
<html lang="en">
<head>
<meta charset="utf-8">
<title>Thornvale Group – Business Card</title>
<link rel="stylesheet" href="https://fonts.googleapis.com/css2?family=Roboto:wght@400;500&display=swap">
<style>
  :root {
    --navy: #1b4a7d;
    --navy-deep: #143a66;
    --ink-blue: #1f4f86;
    --grey-text: #6f7378;
    --rule: #d9dcdf;
    --paper: #ffffff;
    --backdrop: #e9e7e3;
  }
  * { box-sizing: border-box; margin: 0; padding: 0; }
  html, body {
    width: 1200px; height: 950px; overflow: hidden;
    background: var(--backdrop);
    font-family: "Roboto", Arial, sans-serif;
  }
  .sheet { position: relative; width: 1200px; height: 950px; }
  .card {
    position: absolute; left: 230px;
    width: 740px; height: 423px;
    box-shadow: 0 8px 22px rgba(0,0,0,.18);
  }
  .card--front {
    top: 40px;
    background: linear-gradient(160deg, var(--navy) 0%, var(--navy-deep) 100%);
    color: var(--paper);
    display: flex; flex-direction: column; align-items: center; justify-content: center;
  }
  .card--back {
    top: 487px;
    background: var(--paper);
    display: flex;
  }
  .brand {
    display: flex; flex-direction: column; align-items: center;
  }
  .brand__mark {
    width: 64px; height: 64px;
    background: currentColor;
    margin-bottom: 18px;
  }
  .brand__name {
    font-size: 34px; font-weight: 400; line-height: 1.2;
    white-space: nowrap;
  }
  .front__url {
    margin-top: 46px;
    font-size: 17px; font-weight: 400; letter-spacing: 2px;
  }
  .back__brand {
    width: 52%;
    display: flex; align-items: center; justify-content: center;
    padding-top: 30px;
    color: var(--ink-blue);
  }
  .back__brand .brand__name { font-size: 30px; }
  .back__brand .brand__mark { width: 56px; height: 56px; }
  .divider { width: 1px; margin: 40px 0; background: var(--rule); }
  .contact {
    flex: 1;
    padding: 62px 30px 0 34px;
    color: var(--grey-text);
    font-size: 16px; line-height: 1.45;
  }
  .contact__name { color: var(--ink-blue); font-size: 22px; font-weight: 500; }
  .contact__role { margin-bottom: 22px; }
  .contact__lines { margin-bottom: 18px; }
  .contact__list { list-style: none; }
  .contact__list li { display: flex; align-items: center; gap: 10px; margin-bottom: 4px; }
  .contact__list svg { width: 18px; height: 18px; flex: none; }
</style>
</head>
<body>
<div class="sheet">

  <section class="card card--front">
    <div class="brand">
      <span class="brand__mark" aria-hidden="true"></span>
      <span class="brand__name">Thornvale Group</span>
    </div>
    <p class="front__url">www.thornvalegroup.example</p>
  </section>

  <section class="card card--back">
    <div class="back__brand">
      <div class="brand">
        <span class="brand__mark" aria-hidden="true"></span>
        <span class="brand__name">Thornvale Group</span>
      </div>
    </div>
    <div class="divider"></div>
    <div class="contact">
      <p class="contact__name">Peter Castrell</p>
      <p class="contact__role">President</p>
      <div class="contact__lines">
        <p>Thornvale Group LLC</p>
        <p>Finance and Strategy Consulting</p>
        <p>Aviation - Manufacturing - Energy</p>
      </div>
      <ul class="contact__list">
        <li>
          <svg viewBox="0 0 20 20" aria-hidden="true"><circle cx="10" cy="10" r="10" fill="#1f4f86"/><path d="M6.5 5.5c.6-.6 1.4-.4 1.7.2l.8 1.6c.2.5 0 1-.4 1.3l-.6.4c.5 1.2 1.4 2.1 2.6 2.6l.4-.6c.3-.4.8-.6 1.3-.4l1.6.8c.6.3.8 1.1.2 1.7-.9.9-2.2 1.1-3.4.5-2-1-3.6-2.6-4.6-4.6-.6-1.2-.4-2.5.4-3.5z" fill="#fff"/></svg>
          (555) 204-6391
        </li>
        <li>
          <svg viewBox="0 0 20 20" aria-hidden="true"><circle cx="10" cy="10" r="10" fill="#1f4f86"/><rect x="5" y="6.5" width="10" height="7" fill="none" stroke="#fff" stroke-width="1.2"/><path d="M5 6.8l5 3.8 5-3.8" fill="none" stroke="#fff" stroke-width="1.2"/></svg>
          pc@thornvalegroup.example
        </li>
        <li>
          <svg viewBox="0 0 20 20" aria-hidden="true"><circle cx="10" cy="10" r="10" fill="#1f4f86"/><circle cx="10" cy="10" r="5" fill="none" stroke="#fff" stroke-width="1.1"/><ellipse cx="10" cy="10" rx="2.2" ry="5" fill="none" stroke="#fff" stroke-width="1.1"/><path d="M5 10h10" stroke="#fff" stroke-width="1.1"/></svg>
          thornvalegroup.example
        </li>
      </ul>
    </div>
  </section>

</div>
</body>
</html>
```